Business Card for brovaLINK

Create a Business Card with an existing logo for brovaLINK AG. We are a Information Technology company that does consulting and developing SW to automate business processes. The main colors are given from the logo.

Industry/Entity Type

Business

Requirements
Nice to have
• we use a a font style Century Gothic in our documents

```html
<!DOCTYPE html>
<html lang="en">
<head>
<meta charset="utf-8">
<title>brovaLINK – Business Card</title>
<link rel="stylesheet" href="https://fonts.googleapis.com/css2?family=Didact+Gothic&display=swap">
<style>
  :root {
    --page-bg: #e9e6e1;
    --card-white: #ffffff;
    --blue-deep: #1f3f9e;
    --blue-mid: #1e7fd6;
    --blue-light: #3fb2ea;
    --green: #3fb83c;
    --green-light: #a6d92e;
    --ink: #3a3a3c;
    --ink-soft: #6d6d70;
    --back-haze: #c9cfea;
  }
  * { margin: 0; padding: 0; box-sizing: border-box; }
  html, body {
    width: 1200px; height: 1024px; overflow: hidden;
    background: var(--page-bg);
    font-family: "Didact Gothic", "Century Gothic", sans-serif;
  }
  .sheet {
    position: relative; width: 1200px; height: 1024px;
  }
  .card {
    position: absolute; left: 180px; width: 840px; height: 480px;
    border-radius: 28px; overflow: hidden;
    box-shadow: 0 6px 18px rgba(0,0,0,.18);
  }
  .card-front { top: 24px; background: var(--card-white); }
  .card-back { top: 520px; background: var(--back-haze); }
  .card svg.art { position: absolute; inset: 0; }

  .holder { position: absolute; left: 44px; top: 58px; color: #fff; }
  .holder-name { font-size: 36px; letter-spacing: .5px; }
  .holder-role { font-size: 24px; color: var(--green-light); margin-top: 2px; }

  .contact {
    position: absolute; left: 44px; top: 262px;
    color: var(--ink-soft); font-size: 21px; line-height: 29px;
  }
  .contact-address { margin-bottom: 10px; }
  .contact-line { display: flex; align-items: center; gap: 10px; }
  .contact-line svg { width: 18px; height: 18px; flex: none; }

  .brand {
    position: absolute; display: flex; align-items: center; gap: 18px;
  }
  .brand-front { right: 48px; bottom: 62px; }
  .brand-front .brand-name { font-size: 66px; color: var(--ink); }
  .brand-dot { border-radius: 50%; flex: none; }
  .brand-front .brand-dot { width: 58px; height: 58px; background: var(--blue-mid); }

  .brand-back { left: 0; right: 0; top: 180px; justify-content: center; }
  .brand-back .brand-name { font-size: 84px; color: #fff; }
  .brand-back .brand-dot { width: 76px; height: 76px; background: var(--blue-mid); }
  .back-web {
    position: absolute; left: 0; right: 0; top: 296px;
    text-align: center; color: #fff; font-size: 20px; letter-spacing: 1px;
  }
</style>
</head>
<body>
<main class="sheet">

  <section class="card card-front" aria-label="Business card front">
    <svg class="art" width="840" height="480" viewBox="0 0 840 480" aria-hidden="true">
      <defs>
        <linearGradient id="bandBlue" x1="0" y1="0" x2="1" y2="0">
          <stop offset="0" stop-color="var(--blue-deep)"/>
          <stop offset=".55" stop-color="var(--blue-mid)"/>
          <stop offset="1" stop-color="var(--blue-light)"/>
        </linearGradient>
        <linearGradient id="bandGreen" x1="0" y1="0" x2="1" y2="0">
          <stop offset="0" stop-color="var(--green)"/>
          <stop offset="1" stop-color="var(--green-light)"/>
        </linearGradient>
      </defs>
      <path d="M0 0 H840 V8 C640 20 520 120 360 190 C240 240 120 230 0 236 Z" fill="url(#bandGreen)"/>
      <path d="M0 0 H840 V4 C640 12 500 96 340 160 C220 206 110 200 0 210 Z" fill="#fff"/>
      <path d="M0 0 H840 C640 6 500 84 330 148 C210 192 100 190 0 200 Z" fill="url(#bandBlue)"/>
      <path d="M470 0 C600 10 700 0 840 0 V3 C700 10 600 24 470 0 Z" fill="#fff" opacity=".7"/>
    </svg>

    <div class="holder">
      <p class="holder-name">Lukas Brandt</p>
      <p class="holder-role">CEO</p>
    </div>

    <div class="contact">
      <p class="contact-address">Mattenweg 12, 5400 Baden,<br>Switzerland</p>
      <p class="contact-line">
        <svg viewBox="0 0 18 18"><circle cx="9" cy="9" r="9" fill="var(--blue-mid)"/><rect x="5" y="6" width="8" height="6" rx="1" fill="#fff"/></svg>
        +41 56 210 48 35
      </p>
      <p class="contact-line">
        <svg viewBox="0 0 18 18"><circle cx="9" cy="9" r="9" fill="var(--blue-mid)"/><path d="M6 5 L8 7 L7 8.5 C7.8 10 8.5 10.7 10 11.5 L11.5 10.5 L13.5 12.5 L12 14 C8 13 5 10 4.5 6.5 Z" fill="#fff"/></svg>
        +41 79 604 27 19
      </p>
      <p class="contact-line">
        <svg viewBox="0 0 18 18"><circle cx="9" cy="9" r="9" fill="var(--blue-mid)"/><circle cx="9" cy="9" r="5" fill="none" stroke="#fff" stroke-width="1.4"/><path d="M4 9 H14 M9 4 V14" stroke="#fff" stroke-width="1.2"/></svg>
        www.brovalink.ch
      </p>
      <p class="contact-line">
        <svg viewBox="0 0 18 18"><circle cx="9" cy="9" r="9" fill="var(--blue-mid)"/><rect x="4.5" y="5.5" width="9" height="7" fill="none" stroke="#fff" stroke-width="1.3"/><path d="M4.5 5.5 L9 9.5 L13.5 5.5" fill="none" stroke="#fff" stroke-width="1.3"/></svg>
        lukas.brandt@brovalink.ch
      </p>
    </div>

    <div class="brand brand-front">
      <span class="brand-dot"></span>
      <span class="brand-name">brovaLINK</span>
    </div>
  </section>

  <section class="card card-back" aria-label="Business card back">
    <svg class="art" width="840" height="480" viewBox="0 0 840 480" aria-hidden="true">
      <defs>
        <linearGradient id="backBlue" x1="0" y1="0" x2="1" y2="1">
          <stop offset="0" stop-color="var(--blue-deep)"/>
          <stop offset="1" stop-color="var(--blue-light)"/>
        </linearGradient>
        <linearGradient id="backGreen" x1="0" y1="0" x2="1" y2="1">
          <stop offset="0" stop-color="var(--green-light)"/>
          <stop offset="1" stop-color="var(--green)"/>
        </linearGradient>
        <radialGradient id="backGlow" cx=".5" cy=".45" r=".6">
          <stop offset="0" stop-color="#eef0fb"/>
          <stop offset="1" stop-color="var(--back-haze)"/>
        </radialGradient>
      </defs>
      <rect width="840" height="480" fill="url(#backGlow)"/>
      <path d="M0 0 H520 C420 40 300 70 240 160 C190 240 120 300 0 320 Z" fill="url(#backBlue)" opacity=".9"/>
      <path d="M840 480 H300 C420 440 560 420 620 330 C670 250 740 190 840 170 Z" fill="url(#backGreen)" opacity=".85"/>
      <path d="M0 420 C200 400 300 300 420 240 C540 180 700 120 840 110" fill="none" stroke="#fff" stroke-width="4" opacity=".55"/>
      <path d="M0 480 V440 C120 460 220 470 300 480 Z" fill="var(--blue-mid)"/>
    </svg>

    <div class="brand brand-back">
      <span class="brand-name">brovaLINK</span>
      <span class="brand-dot"></span>
    </div>
    <p class="back-web">www.brovalink.ch</p>
  </section>

</main>
</body>
</html>
```